Business Card Design

We need a business card designed for our new company. Prefer a black card with white logo & writing.

Contact Information for Business Card

Ted Galloway, address: 7-4812 Fernhollow Road, Abbotsford, BC, V3K 8R2, Office Phone: 604-712-3390, Cell: 604-947-2164, Email: ted@resinworkshub.ca

Colors

Designer to choose only greyscale colors for use in the design.

```html
<!DOCTYPE html>
<html lang="en">
<head>
<meta charset="utf-8">
<title>Resinworks Hub – Business Card</title>
<link href="https://fonts.googleapis.com/css2?family=Poppins:wght@300;400;700&display=swap" rel="stylesheet">
<style>
  :root {
    --stage: #222223;
    --card: #1f1f21;
    --card-edge: #d8d8d8;
    --ink: #ffffff;
    --ink-soft: #e6e6e6;
    --pattern-dark: #141415;
    --pattern-light: #3a3a3d;
    --art-light: #6a6a6d;
    --art-dark: #1f1f21;
  }
  * { box-sizing: border-box; margin: 0; padding: 0; }
  html, body { width: 1200px; height: 711px; overflow: hidden; }
  body {
    background: var(--stage);
    font-family: "Poppins", sans-serif;
    color: var(--ink);
    position: relative;
  }
  .card {
    position: absolute;
    top: 204px;
    width: 530px;
    height: 303px;
    background: var(--card);
    border-radius: 4px;
    box-shadow: 0 0 0 1px var(--card-edge), 0 14px 30px rgba(0,0,0,.55);
    overflow: hidden;
  }
  .card--front { left: 50px; }
  .card--back { left: 620px; }

  .front-texture {
    position: absolute; inset: 0;
    background: linear-gradient(160deg, var(--pattern-light) 0%, var(--pattern-dark) 55%, var(--pattern-light) 100%);
  }
  .wordmark {
    font-weight: 700;
    color: var(--ink);
    display: flex;
    align-items: center;
    gap: 10px;
    white-space: nowrap;
  }
  .wordmark__square {
    width: 14px; height: 14px;
    border: 2px solid var(--ink);
  }
  .card--front .wordmark {
    position: absolute;
    left: 50%; top: 50%;
    transform: translate(-50%, -50%);
    font-size: 36px;
    letter-spacing: .5px;
  }
  .card--front .wordmark__square { width: 22px; height: 22px; border-width: 3px; }

  .card--back .wordmark {
    position: absolute;
    right: 34px; top: 34px;
    font-size: 24px;
  }
  .contact {
    position: absolute;
    right: 34px; top: 96px;
    text-align: right;
    font-weight: 300;
    font-size: 11.5px;
    line-height: 1.5;
    color: var(--ink-soft);
  }
  .contact__address { margin-bottom: 8px; }
  .contact__row {
    display: flex; justify-content: flex-end; align-items: center; gap: 7px;
  }
  .contact__row svg { width: 11px; height: 11px; fill: none; stroke: var(--ink); stroke-width: 1.6; }
  .bottom-art {
    position: absolute;
    left: 110px; bottom: 0;
    width: 330px; height: 100px;
    background: linear-gradient(90deg, var(--art-light) 0%, var(--art-dark) 100%);
    opacity: .6;
  }
  .person {
    position: absolute;
    left: 22px; bottom: 22px;
    transform-origin: left bottom;
    transform: rotate(-90deg) translateY(100%);
    white-space: nowrap;
  }
  .person__name { display: block; font-size: 24px; font-weight: 300; line-height: 1.1; }
  .person__name strong { font-weight: 700; }
  .person__role { display: block; font-size: 11px; font-weight: 300; }
</style>
</head>
<body>
  <section class="card card--front">
    <div class="front-texture" role="img" aria-label="Repeating embossed chevron pattern in dark grey"></div>
    <div class="wordmark"><span class="wordmark__square"></span>Resinworks Hub</div>
  </section>

  <section class="card card--back">
    <div class="wordmark"><span class="wordmark__square"></span>Resinworks Hub</div>

    <div class="contact">
      <p class="contact__address">7-4812 Fernhollow Road,<br>Abbotsford, BC, V3K 8R2.</p>
      <p class="contact__row">604-712-3390
        <svg viewBox="0 0 12 12"><path d="M3 1.5l2 2-1.2 1.3a6 6 0 0 0 3.4 3.4L8.5 7l2 2-1.3 1.5C5.5 10.5 1.5 6.5 1.5 2.8z"/></svg></p>
      <p class="contact__row">604-947-2164
        <svg viewBox="0 0 12 12"><rect x="3" y="1" width="6" height="10" rx="1"/><path d="M5.5 9h1"/></svg></p>
      <p class="contact__row">www.resinworkshub.ca
        <svg viewBox="0 0 12 12"><circle cx="6" cy="6" r="4.7"/><path d="M1.3 6h9.4M6 1.3c-2.4 2.6-2.4 6.8 0 9.4M6 1.3c2.4 2.6 2.4 6.8 0 9.4"/></svg></p>
      <p class="contact__row">ted@resinworkshub.ca
        <svg viewBox="0 0 12 12"><rect x="1" y="2.5" width="10" height="7"/><path d="M1 2.5l5 4 5-4"/></svg></p>
    </div>

    <div class="bottom-art" role="img" aria-label="Silver decorative illustration along the bottom edge"></div>

    <div class="person">
      <span class="person__name"><strong>Ted</strong> Galloway</span>
      <span class="person__role">Owner</span>
    </div>
  </section>
</body>
</html>
```